Specialised investor in e-mobility and energy wants business card design

We need a business card design that fits our existing corporate design. <The look and feel must be 'sharp'/'clean', dynamic, communicate momentum, professionalism etc (as one would imagine from a firm in the financial sector). We like the idea of a reverse-side of the card that includes the logo, and the name and contact details on the other. We expect the deliverable to be whatever format might be required to be able to get cards printed directly by a service such as kelmo press. Our website is www.zub.capital

```html
<!DOCTYPE html>
<html lang="en">
<head>
<meta charset="utf-8">
<title>ZUB Capital – Business Card</title>
<link href="https://fonts.googleapis.com/css2?family=Arimo:wght@400;700&family=Questrial&display=swap" rel="stylesheet">
<style>
  :root {
    --backdrop: #2b2b2b;
    --card-white: #ffffff;
    --green-dark: #344f25;
    --green-light: #7fb148;
    --text-grey: #3b3b3b;
  }
  * { margin: 0; padding: 0; box-sizing: border-box; }
  html, body { width: 1200px; height: 1059px; overflow: hidden; }
  body { background: var(--backdrop); position: relative; font-family: "Arimo", Arial, sans-serif; }

  .card { position: absolute; border-radius: 18px; overflow: hidden; box-shadow: 0 10px 24px rgba(0,0,0,.55); }

  .card-front { left: 257px; top: 89px; width: 687px; height: 390px; background: var(--card-white); }
  .card-back { left: 254px; top: 547px; width: 693px; height: 393px; background: var(--green-dark); }

  .wordmark { font-family: "Questrial", "Century Gothic", sans-serif; font-weight: 400; white-space: nowrap; position: absolute; line-height: 1.2; }
  .card-front .wordmark { left: 46px; top: 170px; font-size: 48px; color: var(--green-dark); }
  .card-back .wordmark { left: 0; right: 0; top: 136px; text-align: center; font-size: 96px; color: #fff; }

  .divider { position: absolute; left: 343px; top: 111px; width: 1.5px; height: 169px; background: var(--green-dark); }

  .details { position: absolute; left: 374px; top: 106px; color: var(--text-grey); }
  .name { font-weight: 700; font-size: 26px; line-height: 1; letter-spacing: .3px; color: var(--green-dark); }
  .name .surname { color: var(--green-light); }
  .role { font-size: 16px; margin-top: 3px; }
  .address { font-size: 16px; line-height: 20px; margin-top: 11px; }
  .contacts { list-style: none; margin-top: 15px; font-size: 16px; }
  .contacts li { display: flex; align-items: center; height: 23px; }
  .contacts svg { width: 12px; height: 12px; margin-right: 7px; fill: var(--green-light); }

  .footer-band {
    position: absolute; left: 0; right: 0; bottom: 0; height: 47px;
    background: linear-gradient(90deg, var(--green-dark) 0%, var(--green-dark) 70%, var(--green-light) 100%);
  }
</style>
</head>
<body>
  <section class="card card-front" aria-label="Card front">
    <div class="wordmark">ZUB Capital</div>
    <div class="divider"></div>
    <div class="details">
      <h1 class="name">MARTEN <span class="surname">OKORO</span></h1>
      <p class="role">Director/Founder</p>
      <p class="address">1234 Street Name<br>Country Name AB 5748</p>
      <ul class="contacts">
        <li><svg viewBox="0 0 12 12"><path d="M2.5 1l2 2.2-1 1.3c.7 1.5 1.8 2.6 3.3 3.3l1.3-1 2.2 2-1 1.8C5.2 10.4 1.6 6.8 1 1.9z"/></svg>123-555-0190</li>
        <li><svg viewBox="0 0 12 12"><path d="M0 2.5h12v1L6 7 0 3.5z M0 5l6 3.5L12 5v5H0z"/></svg>info@zub.capital</li>
        <li><svg viewBox="0 0 12 12"><circle cx="6" cy="6" r="5.5"/></svg>&nbsp;www.zub.capital</li>
      </ul>
    </div>
    <div class="footer-band" role="img" aria-label="Decorative green curved band along the card's lower edge"></div>
  </section>

  <section class="card card-back" aria-label="Card back">
    <div class="wordmark">ZUB Capital</div>
  </section>
</body>
</html>
```